RESIDENTIAL CONSTRUCTION

We are a company that specializes in building custom residential homes, the design should also emphasize that quality and service is our priority.

Industry/Entity Type

Construction Company

Contact Information for Business Card

Contact Person: Marcus Lindqvist
Company Address: 273 West Alder Ave San Jose , Ca 95380
Phone Number : 408-731-2946
Email Address: Stoneridgehomes517@mailvista.net

Font styles to use
Sans Serif

Colors
ec1f27

Requirements
Must have
• CSLB # 7362015
Nice to have
• needs to have same color as logo i uploaded, we will be printing these on a clear plastic card.

```html
<!DOCTYPE html>
<html lang="en">
<head>
<meta charset="utf-8">
<title>Stoneridge General Builders – Business Card</title>
<link rel="stylesheet" href="https://fonts.googleapis.com/css2?family=Oswald:wght@600&family=Roboto:wght@400;700&display=swap">
<style>
  :root {
    --page-bg: #d9d6d2;
    --card-bg: #eef0f1;
    --card-edge: #c9cdd0;
    --brand-red: #8e1b22;
    --ink: #222325;
    --mark-tone-a: #e4e6e8;
    --mark-tone-b: #d8cfd0;
  }
  html, body {
    margin: 0;
    width: 1200px;
    height: 969px;
    overflow: hidden;
    background: var(--page-bg);
  }
  .business-card {
    position: absolute;
    left: 60px;
    top: 176px;
    width: 1080px;
    height: 617px;
    background: var(--card-bg);
    border: 1px solid var(--card-edge);
    box-sizing: border-box;
    font-family: "Roboto", Arial, sans-serif;
    color: var(--ink);
  }
  .brand-symbol-area {
    position: absolute;
    left: 14px;
    top: 14px;
    width: 530px;
    height: 571px;
    background: linear-gradient(160deg, var(--mark-tone-a), var(--mark-tone-b));
    border-radius: 6px;
  }
  .company-name {
    position: absolute;
    left: 585px;
    top: 64px;
    margin: 0;
    font-family: "Oswald", "Arial Narrow", sans-serif;
    font-weight: 600;
    color: var(--brand-red);
    line-height: 1;
  }
  .company-name .name-main {
    display: block;
    font-size: 84px;
    letter-spacing: 1px;
  }
  .company-name .name-sub {
    display: block;
    margin-top: 10px;
    font-size: 34px;
    letter-spacing: 6.2px;
  }
  .contact-person {
    position: absolute;
    left: 585px;
    top: 268px;
    margin: 0;
    font-size: 33px;
    font-weight: 700;
    color: var(--brand-red);
    letter-spacing: 0.3px;
  }
  .contact-details {
    position: absolute;
    left: 585px;
    top: 330px;
    font-size: 25px;
    line-height: 32px;
  }
  .contact-details p { margin: 0; }
  .license { margin-top: 18px !important; }
  .contact-lines {
    list-style: none;
    margin: 16px 0 0;
    padding: 0;
  }
  .contact-lines li {
    display: flex;
    align-items: center;
    height: 35px;
  }
  .contact-icon {
    width: 22px;
    height: 22px;
    margin-right: 19px;
    fill: var(--brand-red);
    flex: none;
  }
</style>
</head>
<body>
  <main class="business-card">
    <div class="brand-symbol-area" role="img" aria-label="Company symbol: builder's tools and a house outline framed by ruler marks"></div>

    <h1 class="company-name">
      <span class="name-main">STONERIDGE</span>
      <span class="name-sub">GENERAL BUILDERS</span>
    </h1>

    <h2 class="contact-person">MARCUS LINDQVIST</h2>

    <div class="contact-details">
      <p>273 West Alder Ave San Jose</p>
      <p>Ca 95380</p>
      <p class="license">CSLB # 7362015</p>
      <ul class="contact-lines">
        <li>
          <svg class="contact-icon" viewBox="0 0 24 24" aria-hidden="true"><path d="M6.6 10.8a15.1 15.1 0 0 0 6.6 6.6l2.2-2.2c.3-.3.7-.4 1-.2 1.1.4 2.3.6 3.6.6.6 0 1 .4 1 1V20c0 .6-.4 1-1 1A17 17 0 0 1 3 4c0-.6.4-1 1-1h3.5c.6 0 1 .4 1 1 0 1.3.2 2.5.6 3.6.1.3 0 .7-.2 1z"/></svg>
          <span>408-731-2946</span>
        </li>
        <li>
          <svg class="contact-icon" viewBox="0 0 24 24" aria-hidden="true"><path d="M2 5h20v14H2z M3.5 6.5 12 13l8.5-6.5" fill="var(--brand-red)"/><path d="M3 6l9 7 9-7" fill="none" stroke="var(--card-bg)" stroke-width="1.6"/></svg>
          <span>Stoneridgehomes517@mailvista.net</span>
        </li>
        <li>
          <svg class="contact-icon" viewBox="0 0 24 24" aria-hidden="true"><circle cx="12" cy="12" r="10"/><path d="M2 12h20M12 2c3 3 3 17 0 20M12 2c-3 3-3 17 0 20" fill="none" stroke="var(--card-bg)" stroke-width="1.5"/></svg>
          <span>www.stoneridgebuilders.net</span>
        </li>
      </ul>
    </div>
  </main>
</body>
</html>
```